Design 4 pages for an event discovery website

This is a contest for the design of 4 pages for an events discovery website. The feature is part of the new sign-up process.

Please see the attached document for a full scope, mockups and the parent category icons.

Target Market(s)

18-35 Australian event goers

Industry/Entity Type

Events

Number of Pages Required

4 page

```html
<!DOCTYPE html>
<html lang="en">
<head>
<meta charset="utf-8">
<title>Evenlo — Sign Up</title>
<link href="https://fonts.googleapis.com/css2?family=Open+Sans:wght@400;600;700&family=Arimo:wght@400&display=swap" rel="stylesheet">
<style>
  :root{
    --bg-deep:#22222c;
    --bg-mid:#2b2b36;
    --glow-teal:#2f6a5a;
    --glow-rose:#7a4a55;
    --glow-amber:#8a7a5a;
    --text:#ffffff;
    --text-soft:#e8e8ee;
    --rule:#1a1a22;
    --panel:#3d4247;
    --panel-edge:#2a2d31;
    --button-top:#4a66a8;
    --button-bottom:#3a5496;
    --button-edge:#2c3f73;
  }
  *{margin:0;padding:0;box-sizing:border-box}
  html,body{width:1200px;height:679px;overflow:hidden;background:var(--bg-deep)}
  body{position:relative;font-family:"Open Sans",Arial,sans-serif;color:var(--text)}

  .backdrop{
    position:absolute;inset:0;
    background:
      radial-gradient(ellipse 360px 200px at 980px 190px, rgba(138,122,90,.45), transparent 70%),
      radial-gradient(ellipse 300px 220px at 1060px 90px, rgba(122,74,85,.5), transparent 70%),
      radial-gradient(ellipse 520px 160px at 120px 600px, rgba(47,106,90,.55), transparent 70%),
      radial-gradient(ellipse 420px 120px at 380px 470px, rgba(47,106,90,.35), transparent 70%),
      linear-gradient(180deg,var(--bg-mid),var(--bg-deep));
  }

  .site-header{position:absolute;left:0;top:0;width:1200px;height:106px;border-bottom:2px solid var(--rule)}
  .brand{position:absolute;left:141px;top:34px;font-size:29px;font-weight:600;letter-spacing:.5px}
  .search{
    position:absolute;left:664px;top:33px;width:235px;height:42px;
    border:1.5px solid var(--text);border-radius:21px;
    font-family:"Arimo",Arial,sans-serif;font-size:14px;font-weight:700;
    padding:12px 0 0 22px;
  }
  .search svg{position:absolute;right:22px;top:14px}
  .nav{position:absolute;top:44px;font-size:14px;font-weight:600}
  .nav-signup{left:920px}
  .nav-divider{left:987px}
  .nav-login{left:1016px}

  .signup-panel{
    position:absolute;left:162px;top:185px;width:327px;height:310px;
    background:linear-gradient(180deg,#444a50,var(--panel));
    border:1px solid var(--panel-edge);border-radius:3px;
    box-shadow:0 4px 0 #2e3236,0 6px 0 #1f2225,0 14px 22px rgba(20,80,60,.45);
  }
  .panel-handle{position:absolute;left:110px;top:24px;width:107px;height:12px;border-radius:6px;
    background:linear-gradient(180deg,#e0e0e0,#888);border:2px solid #1b1b1b}
  .panel-title{position:absolute;left:0;right:0;top:48px;text-align:center;font-size:24px;font-weight:700;
    text-shadow:0 3px 4px rgba(0,0,0,.7)}
  .connect-button{
    position:absolute;left:21px;top:106px;width:287px;height:137px;
    background:linear-gradient(180deg,var(--button-top),var(--button-bottom));
    border:1px solid var(--button-edge);box-shadow:0 2px 6px rgba(0,0,0,.5);
  }
  .connect-mark{position:absolute;left:22px;top:50px;width:26px;height:26px;border:3px solid var(--text);border-radius:50%}
  .connect-divider{position:absolute;left:67px;top:50px;width:1px;height:48px;background:#2d4278}
  .connect-small{position:absolute;left:85px;top:32px;font-size:21px;font-weight:600}
  .connect-large{position:absolute;left:85px;top:58px;font-size:39px;font-weight:600}

  .alt-signup{position:absolute;left:163px;top:534px;display:flex;align-items:center;gap:14px}
  .tick-box{width:19px;height:19px;border-radius:3px;background:linear-gradient(#d8d8d8,#9a9a9a);border:1px solid #222;display:flex;align-items:center;justify-content:center}
  .alt-link{font-size:17px;font-weight:600;text-decoration:underline;text-underline-offset:3px}

  .benefits{position:absolute;left:591px;top:212px}
  .benefits h2{font-size:27px;font-weight:700;margin-bottom:20px}
  .benefit-list{list-style:none;font-family:"Arimo",Arial,sans-serif;font-size:14px}
  .benefit-list li{position:relative;padding-left:18px;height:35.6px}
  .benefit-list svg{position:absolute;left:-5px;top:3px}

  .site-footer{position:absolute;left:0;top:601px;width:1200px;height:78px;border-top:2px solid var(--rule)}
  .copyright{position:absolute;left:141px;top:35px;font-family:"Arimo",Arial,sans-serif;font-size:12px}
  .social{position:absolute;left:840px;top:26px;display:flex;gap:10px}
  .social span{width:37px;height:37px;border:1.5px solid var(--text);border-radius:50%}
</style>
</head>
<body>
  <div class="backdrop" role="img" aria-label="Dark abstract background with soft teal, rose and amber light streaks"></div>

  <header class="site-header">
    <div class="brand">EVENLO</div>
    <div class="search">Search
      <svg width="12" height="12" viewBox="0 0 12 12"><circle cx="5" cy="5" r="3.6" fill="none" stroke="#fff" stroke-width="2"/><line x1="7.6" y1="7.6" x2="11" y2="11" stroke="#fff" stroke-width="2.2"/></svg>
    </div>
    <a class="nav nav-signup">SIGN UP</a>
    <span class="nav nav-divider">|</span>
    <a class="nav nav-login">LOG IN</a>
  </header>

  <section class="signup-panel">
    <div class="panel-handle"></div>
    <h1 class="panel-title">SIGN UP</h1>
    <div class="connect-button">
      <span class="connect-mark"></span>
      <span class="connect-divider"></span>
      <span class="connect-small">Connect With</span>
      <span class="connect-large">Friendnet</span>
    </div>
  </section>

  <div class="alt-signup">
    <span class="tick-box"><svg width="12" height="10" viewBox="0 0 12 10"><path d="M1 5l3.5 3.5L11 1.5" fill="none" stroke="#333" stroke-width="2.4"/></svg></span>
    <span class="alt-link">Click Here to Sign up with Friendnet</span>
  </div>

  <section class="benefits">
    <h2>OUR BENEFITS</h2>
    <ul class="benefit-list">
      <li><svg width="9" height="12" viewBox="0 0 9 12"><path d="M2 1l5 5-5 5" fill="none" stroke="#fff" stroke-width="2.4"/></svg>Get personalised event recommendations</li>
      <li><svg width="9" height="12" viewBox="0 0 9 12"><path d="M2 1l5 5-5 5" fill="none" stroke="#fff" stroke-width="2.4"/></svg>Get notified about your favourite events - never miss out again</li>
      <li><svg width="9" height="12" viewBox="0 0 9 12"><path d="M2 1l5 5-5 5" fill="none" stroke="#fff" stroke-width="2.4"/></svg>Follow all your favourite artists, musicians, teams and players in one place</li>
      <li><svg width="9" height="12" viewBox="0 0 9 12"><path d="M2 1l5 5-5 5" fill="none" stroke="#fff" stroke-width="2.4"/></svg>Follow your favourite local venues to know everything happening there</li>
      <li><svg width="9" height="12" viewBox="0 0 9 12"><path d="M2 1l5 5-5 5" fill="none" stroke="#fff" stroke-width="2.4"/></svg>Get curated news and feature content on your favourite artists (coming soon)</li>
      <li><svg width="9" height="12" viewBox="0 0 9 12"><path d="M2 1l5 5-5 5" fill="none" stroke="#fff" stroke-width="2.4"/></svg>Invite your mates to events via Friendnet (FN sign-up only)</li>
    </ul>
  </section>

  <footer class="site-footer">
    <p class="copyright">© Copy Rights 2015 Evenlo.All Rights Reserved.</p>
    <div class="social"><span></span><span></span><span></span><span></span><span></span></div>
  </footer>
</body>
</html>
```